Restyle corporate identity (+ logo) for a road construction company

We need a new logo and stationary design for our company VARNOK path. VARNOK path® increases the road base strength, while reducing major costs and time of road construction. Attached some examples of the current design.

Our wishes for the new logo:
- Business look
- Style sheet
- Modern

More information: www.varnokpath.example
Updates

Target Market(s)

Government

Industry/Entity Type

Construction

Requirements
Must have
• Logo (with road sign) + text

```html
<!DOCTYPE html>
<html lang="en">
<head>
<meta charset="utf-8">
<title>VARNOK path – Business Card</title>
<link rel="stylesheet" href="https://fonts.googleapis.com/css2?family=Open+Sans:wght@400;600&display=swap">
<style>
  :root {
    --backdrop: #8e8e8e;
    --card-paper: #f2f2f2;
    --brand-blue: #0a78dc;
    --ink-dark: #4a4a4a;
    --ink-soft: #8a8a8a;
    --rule: #6a6a6a;
    --on-blue: #eef4fb;
    --faint-on-blue: rgba(255, 255, 255, 0.12);
  }
  * { margin: 0; padding: 0; box-sizing: border-box; }
  html, body {
    width: 1105px;
    height: 1200px;
    overflow: hidden;
    background: var(--backdrop);
    font-family: "Open Sans", Arial, sans-serif;
  }
  .card {
    position: absolute;
    left: 182px;
    width: 747px;
    height: 426px;
    overflow: hidden;
  }
  .card--front { top: 119px; background: var(--card-paper); }
  .card--back { top: 637px; background: var(--brand-blue); }

  /* Front */
  .wordmark {
    position: absolute;
    right: 46px;
    top: 56px;
    display: flex;
    align-items: center;
    gap: 14px;
    color: var(--brand-blue);
    font-weight: 600;
    text-align: right;
    line-height: 1;
  }
  .wordmark__square {
    width: 56px;
    height: 56px;
    background: var(--brand-blue);
    border-radius: 6px;
  }
  .wordmark__text { font-size: 40px; letter-spacing: 1px; }
  .wordmark__text span { display: block; font-size: 34px; letter-spacing: 9px; margin-right: -9px; margin-top: 6px; }

  .accent-bar {
    position: absolute;
    left: 0;
    top: 233px;
    width: 15px;
    height: 55px;
    background: var(--brand-blue);
  }
  .person { position: absolute; left: 46px; top: 236px; }
  .person__name {
    font-size: 26px;
    font-weight: 600;
    color: var(--brand-blue);
    line-height: 1.2;
  }
  .person__role { font-size: 19px; color: var(--ink-soft); line-height: 1.3; }

  .contact {
    position: absolute;
    left: 46px;
    top: 308px;
    list-style: none;
    font-size: 19px;
    color: var(--ink-dark);
    line-height: 28.5px;
    white-space: nowrap;
  }
  .contact li { display: flex; align-items: center; gap: 10px; }
  .contact svg { width: 18px; height: 18px; fill: var(--brand-blue); flex: none; }

  .divider {
    position: absolute;
    left: 338px;
    top: 341px;
    width: 2px;
    height: 51px;
    background: var(--rule);
  }
  .address {
    position: absolute;
    left: 360px;
    top: 336px;
    font-style: normal;
    font-size: 19px;
    color: var(--ink-dark);
    line-height: 28.5px;
    white-space: nowrap;
  }

  /* Back */
  .backdrop-square {
    position: absolute;
    left: 35px;
    top: 33px;
    width: 364px;
    height: 366px;
    border-radius: 44px;
    background: var(--faint-on-blue);
  }
  .back-brand {
    position: absolute;
    right: 56px;
    top: 226px;
    text-align: right;
    color: var(--on-blue);
    font-weight: 600;
    line-height: 1;
  }
  .back-brand__name { font-size: 78px; letter-spacing: 1px; }
  .back-brand__sub { font-size: 56px; letter-spacing: 20px; margin-right: -20px; margin-top: 8px; font-weight: 400; }
  .back-brand__url { font-size: 19px; letter-spacing: 1px; margin-top: 12px; font-weight: 400; }
</style>
</head>
<body>
  <section class="card card--front">
    <div class="wordmark">
      <div class="wordmark__square"></div>
      <div class="wordmark__text">VARNOK<span>PATH</span></div>
    </div>

    <div class="accent-bar"></div>
    <div class="person">
      <p class="person__name">MAREN HOLT</p>
      <p class="person__role">CEO/Founder</p>
    </div>

    <ul class="contact">
      <li>
        <svg viewBox="0 0 24 24" aria-hidden="true"><path d="M6.6 10.8a15.1 15.1 0 0 0 6.6 6.6l2.2-2.2a1 1 0 0 1 1-.25 11.4 11.4 0 0 0 3.6.57 1 1 0 0 1 1 1V20a1 1 0 0 1-1 1A17 17 0 0 1 3 4a1 1 0 0 1 1-1h3.5a1 1 0 0 1 1 1c0 1.25.2 2.45.57 3.57a1 1 0 0 1-.25 1z"/></svg>
        612 804 3917
      </li>
      <li>
        <svg viewBox="0 0 24 24" aria-hidden="true"><path d="M2 5h20v2l-10 6L2 7z"/><path d="M2 8l10 6 10-6v11H2z"/></svg>
        info@varnokpath.example
      </li>
      <li>
        <svg viewBox="0 0 24 24" aria-hidden="true"><circle cx="12" cy="12" r="10"/><path d="M12 2v20M2 12h20M5 6c4 2 10 2 14 0M5 18c4-2 10-2 14 0" stroke="#f2f2f2" stroke-width="1.4" fill="none"/></svg>
        www.varnokpath.example
      </li>
    </ul>

    <div class="divider"></div>
    <address class="address">
      Kadeweg 48<br>
      2511 AB Zandhaven, The Netherlands
    </address>
  </section>

  <section class="card card--back">
    <div class="backdrop-square"></div>
    <div class="back-brand">
      <p class="back-brand__name">VARNOK</p>
      <p class="back-brand__sub">PATH</p>
      <p class="back-brand__url">www.varnokpath.example</p>
    </div>
  </section>
</body>
</html>
```